Klasse Designer. Ehrliche Arbeit. Exemplarischer Einsatz. Ich bin sehr zufrieden, einen solchen Designer gefunden zu haben. Es gabt noch gute, aber KobaltWerk und... ist unschlagbar gewesen. Es ist sehr selten Leute zu finden, welche solche Projekte mit einem solchen Einsatz erledigen. Leider gab es auch andere im Projekt, die welche nur Vorschläge machten und "NULL" Einsatz hatten. Ich kann nur sagen, KobaltWerk und... ist eine Wucht. Und ich bin ein sehr, sehr anspruchsvoller Kunde. Aber dieser Designer hat in ständigem Austausch alles zu meiner vollsten Zufriedenheit angepasst in stundenlanger Arbeit. Bedauerlicherweise kann man nur 5 Sterne geben. Der Designer hätte ********** 10 verdient.
Zielgruppe
Habe ein Buch geschrieben und brauche ein Cover
Aufgabenstellung
Hallo, liebe Designer,
Projekt ist fast fertig.

```html
<!DOCTYPE html>
<html lang="de">
<head>
<meta charset="utf-8">
<title>Die Oren – Buchcover</title>
<link href="https://fonts.googleapis.com/css2?family=Josefin+Sans:wght@300&family=Roboto:wght@300&display=swap" rel="stylesheet">
<style>
  :root {
    --page-bg: #d9d6ee;
    --cover-green: #1f8a6a;
    --cover-teal: #2f6fa8;
    --cover-violet: #6a2ff0;
    --cover-indigo: #3a2bd6;
    --cover-navy: #2a2496;
    --ink-light: #e8e6f6;
    --gold-light: #f0cf7a;
    --gold-mid: #c9963a;
    --gold-dark: #8a6220;
  }
  * { margin: 0; padding: 0; box-sizing: border-box; }
  html, body {
    width: 1200px;
    height: 1200px;
    overflow: hidden;
    background: var(--page-bg);
  }
  .book-cover {
    position: absolute;
    left: 225px;
    top: 60px;
    width: 750px;
    height: 1080px;
    background: linear-gradient(180deg,
      var(--cover-green) 0%,
      var(--cover-teal) 20%,
      var(--cover-violet) 37%,
      var(--cover-indigo) 62%,
      var(--cover-navy) 100%);
    color: var(--ink-light);
    text-align: center;
  }
  .book-title {
    position: absolute;
    top: 150px;
    width: 100%;
    font-family: "Josefin Sans", sans-serif;
    font-weight: 300;
    font-size: 40px;
    letter-spacing: 8px;
  }
  .book-subtitle {
    position: absolute;
    top: 212px;
    width: 100%;
    font-family: "Roboto", sans-serif;
    font-weight: 300;
    font-size: 26px;
    letter-spacing: 1.5px;
  }
  .emblem-art {
    position: absolute;
    left: 210px;
    top: 340px;
    width: 330px;
    height: 330px;
  }
  .book-author {
    position: absolute;
    top: 895px;
    width: 100%;
    font-family: "Josefin Sans", sans-serif;
    font-weight: 300;
    font-size: 30px;
    letter-spacing: 5px;
  }
</style>
</head>
<body>
  <main class="book-cover">
    <h1 class="book-title">DIE OREN</h1>
    <p class="book-subtitle">Berufen für alle Zeiten</p>
    <svg class="emblem-art" viewBox="0 0 330 330" role="img" aria-label="Goldene Schlange, die sich in den eigenen Schwanz beißt, als Ring um ein Emblem">
      <defs>
        <radialGradient id="gold-glow" cx="0.5" cy="0.5" r="0.5">
          <stop offset="0.6" stop-color="var(--gold-mid)" stop-opacity="0.25"/>
          <stop offset="0.85" stop-color="var(--gold-light)" stop-opacity="0.9"/>
          <stop offset="1" stop-color="var(--gold-dark)" stop-opacity="0.8"/>
        </radialGradient>
      </defs>
      <circle cx="165" cy="170" r="158" fill="url(#gold-glow)"/>
    </svg>
    <p class="book-author">LORENZ MAIWALD</p>
  </main>
</body>
</html>
```